New Webpage for High Class Expert Witness Services Company

We are looking for a minimalist design for a webpage that just has our logo and an entry form offer to connect with one of our Liaisons.
The entry form should just ask for Name, Email, Contact Info and Description of Project.

Company Name is: The Marlowe Crest Advisory Services

Number of Pages Required

1 page

```html
<!DOCTYPE html>
<html lang="en">
<head>
<meta charset="utf-8">
<title>Marlowe Crest Advisory Services — Connect With a Liaison</title>
<link rel="stylesheet" href="https://fonts.googleapis.com/css2?family=Cinzel:wght@500;600&family=Inter:wght@400&display=swap">
<style>
  :root {
    --page-bg: #1f1f1f;
    --scene-dark: #17191a;
    --scene-warm: #3a3226;
    --header-bg: #000000;
    --card-bg: rgba(48, 48, 48, 0.86);
    --text-main: #ffffff;
    --text-soft: #d6d6d6;
    --rule: #6a6a6a;
    --button-light: #f2f2f2;
    --button-mid: #b9b9bd;
    --button-text: #111111;
    --footer-bg: #000000;
  }
  * { box-sizing: border-box; margin: 0; padding: 0; }
  html, body { width: 1200px; height: 608px; overflow: hidden; }
  body {
    position: relative;
    background: var(--page-bg);
    font-family: "Inter", Arial, sans-serif;
    color: var(--text-main);
  }
  .backdrop {
    position: absolute; inset: 0 0 39px 0;
    background:
      radial-gradient(ellipse 180px 260px at 1090px 330px, var(--scene-warm), transparent 70%),
      radial-gradient(ellipse 220px 300px at 150px 320px, #2c2d2e, transparent 75%),
      linear-gradient(180deg, #262626 0%, var(--scene-dark) 60%, #221d17 100%);
  }
  .site-header {
    position: absolute; left: 208px; top: 19px; width: 784px; height: 62px;
    background: var(--header-bg); border-radius: 3px;
    display: flex; align-items: center; justify-content: center;
  }
  .brand {
    display: flex; align-items: center; gap: 9px;
    font-family: "Cinzel", Georgia, serif; font-weight: 500;
    font-size: 15px; letter-spacing: 0.04em; color: var(--text-main);
  }
  .brand-mark { width: 14px; height: 14px; background: var(--text-main); }
  .liaison-card {
    position: absolute; left: 208px; top: 101px; width: 784px; height: 444px;
    background: var(--card-bg);
  }
  .corner { position: absolute; bottom: 0; width: 8px; height: 8px; border-bottom: 1px solid #cfcfcf; }
  .corner-left { left: 0; border-left: 1px solid #cfcfcf; }
  .corner-right { right: 0; border-right: 1px solid #cfcfcf; }
  .card-title {
    position: absolute; top: 37px; width: 100%; text-align: center;
    font-family: "Cinzel", Georgia, serif; font-weight: 500;
    font-size: 26px; letter-spacing: -0.01em;
  }
  .card-intro {
    position: absolute; top: 72px; width: 100%; text-align: center;
    font-size: 10px; color: var(--text-soft);
  }
  .title-rule {
    position: absolute; top: 98px; left: 375px; width: 34px; height: 1px; background: var(--text-soft);
  }
  .liaison-form { position: absolute; left: 115px; top: 124px; width: 554px; }
  .field {
    display: flex; align-items: center; gap: 7px;
    height: 47px; border-bottom: 1px solid var(--rule);
    padding-top: 4px; align-items: flex-start;
  }
  .field svg { flex: none; width: 11px; height: 11px; margin-top: 6px; }
  .field input, .field textarea {
    flex: 1; background: transparent; border: 0; outline: 0; resize: none;
    font-family: "Inter", Arial, sans-serif; font-size: 10.5px; color: var(--text-main);
    padding-top: 4px;
  }
  .field input::placeholder, .field textarea::placeholder { color: var(--text-soft); opacity: 1; }
  .field-first { height: 32px; }
  .field-first svg { margin-top: 0; }
  .field-first input { padding-top: 0; }
  .field-description { height: 72px; }
  .field-description textarea { height: 60px; }
  .submit-button {
    position: absolute; left: 207px; top: 341px; width: 140px; height: 38px;
    border: 0; cursor: pointer;
    background: linear-gradient(90deg, var(--button-light), var(--button-mid));
    font-family: "Cinzel", Georgia, serif; font-weight: 600; font-size: 12px;
    color: var(--button-text);
  }
  .site-footer {
    position: absolute; left: 0; bottom: 0; width: 100%; height: 39px;
    background: var(--footer-bg);
    display: flex; align-items: center; justify-content: center;
    font-size: 10px; color: var(--text-soft);
  }
</style>
</head>
<body>
  <div class="backdrop" role="img" aria-label="Darkened photograph of the Capitol dome and a uniformed soldier"></div>

  <header class="site-header">
    <div class="brand"><span class="brand-mark"></span>Marlowe Crest Advisory Services</div>
  </header>

  <main class="liaison-card">
    <h1 class="card-title">CONNECT WITH A LIAISON</h1>
    <p class="card-intro">Tell Us About Your Project &amp; Our Team Will Reach Out To You Shortly.</p>
    <div class="title-rule"></div>

    <form class="liaison-form">
      <label class="field field-first">
        <svg viewBox="0 0 12 12" fill="none" stroke="#d6d6d6" stroke-width="1"><circle cx="6" cy="3.5" r="2.5"/><path d="M1.5 11.5v-1.5a3 3 0 0 1 3-3h3a3 3 0 0 1 3 3v1.5z"/></svg>
        <input type="text" placeholder="Your Name*">
      </label>
      <label class="field">
        <svg viewBox="0 0 12 12" fill="none" stroke="#d6d6d6" stroke-width="1"><rect x="0.5" y="2" width="11" height="8" rx="1"/><path d="M0.5 2.5 6 6.5l5.5-4"/></svg>
        <input type="email" placeholder="Email Address*">
      </label>
      <label class="field">
        <svg viewBox="0 0 12 12" fill="none" stroke="#d6d6d6" stroke-width="1"><rect x="2.5" y="0.5" width="7" height="11" rx="1"/><path d="M5 9.5h2"/></svg>
        <input type="tel" placeholder="Number*">
      </label>
      <label class="field field-description">
        <svg viewBox="0 0 12 12" fill="none" stroke="#d6d6d6" stroke-width="1"><path d="M6 1.5H1.5v9h9V6"/><path d="M9.5 0.8 11.2 2.5 6 7.7H4.3V6z"/></svg>
        <textarea placeholder="Description of Project*"></textarea>
      </label>
    </form>

    <button class="submit-button" type="submit">SUBMIT REQUEST</button>

    <span class="corner corner-left"></span>
    <span class="corner corner-right"></span>
  </main>

  <footer class="site-footer">© Marlowe Crest Advisory Services</footer>
</body>
</html>
```